Home Page for a Swiss based start up company, trading Natural & Health food ingredients (B2B)

I would like to create a home page for my new start up company (Veltrana Swiss AG), the main field of activity is the trading and marketing of Natural and Health food ingredients towards the functional Food and Food supplements industry. (B2B).
Target Market : Functional Food and Food Supplement Manufacturers (B2B) based in Switzerland and Europe
The values I would like to convey are :
- sourcing of natural and health ingredients, (example : natural plant extracts, Omega 3, plant proteins, natural vitamins, vegan food ingredients...etc)
- Health & Nutritional Health
- Eco-friendly and Sustainability
- High Quality Standard in term of products and logistic services
- Trust and reliability
- Flexibility & speed to market
-Technical advice for the development of new products

The site will be translated in 3 languages (German, French, English)
Number of web pages : 5 : Home, About us, Products, Our Services, Contact

See here below attached Logo file.

Here some link of websites which can be taken as benchmark or source of inspiration
- https://quorbelix.com
- https://www.dralvimo.com/

Target Market(s)

Manufacturers of Functional Foods and Food Supplements in Switzerland and Europe (B2B)

Industry/Entity Type

B2B Trading of Natural & Health Ingredients

Coding

Number of Pages Required

Font styles to use
Sans Serif

Colors
0054AA
0677BA
7BADD7
CADEEF
E8F1F8
0094D4
00A9DD
6FCCEA
C7EBF8
E9F6FB
00AB8E
00BBA5
67D7C9
C6EFE9
E9F9F6
59FF00
82FF00
B8FF75
E3FFCB
F4FFEA
FFF300
FFF600
FEFA6F
FFFEC7
FFFEE8
FFC000
F8CF3A
FAE287
FDF2CF
FEFAEE
F0912C
F2A743
F7CA91
FBE8D2
FDF5EE
EE7325
F08F49
F5BC92
FAE3D3
FDF4ED

Requirements
Must have
• inspiration towards nature, sustainability, vegan food, functional food & beverages, food supplements, nutritional health, low carbon footprint
Should not have
• animals, chemistry, food additives

```html
<!DOCTYPE html>
<html lang="en">
<head>
<meta charset="utf-8">
<title>Veltrana Swiss AG – Natural &amp; Functional Ingredients Trader</title>
<link href="https://fonts.googleapis.com/css2?family=Outfit:wght@300;400;500;600;700&display=swap" rel="stylesheet">
<style>
:root{
  --green:#6c8b0b;
  --green-dark:#5a760a;
  --ink:#1f1f1f;
  --text:#555;
  --muted:#8a8a8a;
  --cream:#fbf0d3;
  --orange:#f08a2c;
  --orange-deep:#ee7325;
  --grey-bg:#f2f2f2;
  --line:#e4e4e4;
  --white:#fff;
}
*{box-sizing:border-box;margin:0;padding:0}
html,body{width:1200px;height:4000px;overflow:hidden}
body{font-family:"Outfit",sans-serif;color:var(--ink);background:var(--white);position:relative}
.wrap{position:absolute;left:156px;width:888px}
section,header,footer,.topbar{position:absolute;left:0;width:1200px}
.btn{display:inline-flex;align-items:center;gap:14px;background:var(--green);color:#fff;font-weight:600;font-size:19px;border-radius:0 28px 28px 0;padding:0 14px 0 26px;position:absolute}
.btn .arrow{width:24px;height:24px;border-radius:50%;background:#fff;display:flex;align-items:center;justify-content:center}
.eyebrow{color:var(--green);font-size:16px;text-align:center;position:absolute;width:1200px;left:0}
.title{font-size:42px;font-weight:600;text-align:center;position:absolute;width:1200px;left:0;letter-spacing:.5px}
/* top bar */
.topbar{top:0;height:23px;background:var(--green);color:#fff;font-size:12px;font-weight:500}
.topbar .wrap{top:4px;display:flex;justify-content:space-between}
.topbar .social{display:flex;gap:14px;margin-right:8px}
.topbar .social span{width:12px;height:12px;border-radius:50%;background:#fff;opacity:.9}
/* header */
header{top:23px;height:75px;border-bottom:1px solid var(--line)}
.logo{position:absolute;left:156px;top:20px;display:flex;align-items:center;gap:8px}
.logo .mark{width:30px;height:30px;border-radius:50%;border:3px solid var(--green)}
.logo .name{font-size:19px;font-weight:600;color:var(--green)}
.nav-divider{position:absolute;left:360px;top:0;width:1px;height:75px;background:var(--line)}
nav{position:absolute;left:386px;top:29px;display:flex;gap:24px;font-size:13px;font-weight:500}
.head-tools{position:absolute;left:878px;top:21px;display:flex;gap:16px;align-items:center}
.tool{width:34px;height:34px;background:#eef0e8;display:flex;align-items:center;justify-content:center}
.head-tools .sep{width:1px;height:75px;background:var(--line);margin:-21px 4px 0}
.flag{width:18px;height:12px;background:linear-gradient(#b22 0 50%,#fff 50%);outline:1px solid #ccd}
/* hero */
.hero{top:98px;height:515px;background:linear-gradient(180deg,#c8a45a 0%,#8f8a4a 25%,#4f7a2a 55%,#3b6a1c 100%)}
.hero-label{position:absolute;top:128px;width:1200px;text-align:center;color:#fff;font-size:17px}
.hero h1{position:absolute;top:165px;width:1200px;text-align:center;color:#fff;font-size:54px;font-weight:600;line-height:60px;letter-spacing:1px}
.hero .btn{left:498px;top:324px;height:56px;border-radius:0 28px 28px 0}
.slide-arrow{position:absolute;top:236px;width:40px;height:40px;border-radius:50%;background:#fff;display:flex;align-items:center;justify-content:center}
/* perks */
.perks{top:677px;height:80px}
.perk{position:absolute;top:0;width:280px;height:79px;background:var(--cream);border-radius:40px 0 0 40px;display:flex;align-items:center;gap:16px;padding-left:20px}
.perk b{display:block;font-size:18px;font-weight:600}
.perk small{font-size:12px;color:var(--muted)}
/* values */
.values{top:820px;height:546px;background:var(--grey-bg)}
.bottle{position:absolute;left:500px;top:190px;width:210px;height:356px;background:radial-gradient(ellipse at 50% 70%,#6a8a3a 0%,#5a3a1a 35%,rgba(242,242,242,0) 70%)}
.pill{position:absolute;width:325px;height:68px;background:#fff;border-radius:34px;display:flex;align-items:center;gap:14px;padding-left:14px;font-size:15px;font-weight:500;line-height:20px}
.pill .ico{width:46px;height:46px;border-radius:50%;border:1px solid var(--line);display:flex;align-items:center;justify-content:center;flex:none}
/* ingredients */
.ingredients{top:1366px;height:560px}
.ing-card{position:absolute;top:163px;width:280px;height:209px}
.ing-card .photo{width:100%;height:209px}
.ing-card .tag{position:absolute;left:40px;right:40px;top:191px;height:38px;border-radius:19px;background:var(--cream);font-size:16px;font-weight:500;display:flex;align-items:center;justify-content:center}
.ingredients .btn{left:512px;top:442px;height:55px;border-radius:0 28px 28px 0}
/* offer */
.offer{top:1926px;height:405px;background:linear-gradient(90deg,#e9eef1 0%,#eef1f3 55%,#f3f3f3 100%)}
.offer-photo{position:absolute;left:667px;top:0;width:533px;height:405px;background:radial-gradient(circle at 75% 65%,#f2a743 0%,#e89a3a 18%,#b9c9a0 40%,#7a9a4a 70%,#eef1f3 100%)}
.offer h2{position:absolute;left:156px;top:54px;font-size:43px;font-weight:600;line-height:46px}
.offer .grab{position:absolute;left:156px;top:164px;color:var(--green);font-size:17px;font-weight:500}
.count{position:absolute;left:156px;top:196px;display:flex;gap:18px}
.count div{text-align:center;width:52px}
.count span{display:flex;width:34px;height:34px;margin:0 auto;border-radius:50%;background:#fff;align-items:center;justify-content:center;font-size:15px}
.count small{display:block;font-size:11px;margin-top:8px}
.offer .btn{left:156px;top:292px;height:55px}
/* about */
.about{top:2331px;height:494px}
.about-photo{position:absolute;left:155px;top:64px;width:399px;height:366px;background:linear-gradient(135deg,#3f6a2a,#2f5a22 45%,#8a2a2a 70%,#1e3a22)}
.about .eyebrow{left:613px;top:82px;width:auto;text-align:left}
.about h2{position:absolute;left:613px;top:104px;font-size:42px;font-weight:600;line-height:46px}
.about p{position:absolute;left:611px;top:222px;width:430px;font-size:14px;line-height:22.5px;color:var(--text);font-weight:300}
.about .btn{left:611px;top:360px;height:56px}
/* news */
.news{top:2825px;height:610px;background:#f6f6f6}
.post{position:absolute;top:191px;width:281px}
.post .photo{height:208px}
.post .date{position:absolute;left:28px;top:-28px;width:50px;height:50px;border-radius:50%;background:#fff;font-size:13px;font-weight:600;line-height:14px;display:flex;flex-direction:column;align-items:center;justify-content:center}
.post .meta{margin-top:20px;font-size:14px;color:var(--muted)}
.post .meta i{font-style:normal;margin:0 8px}
.post h3{margin-top:14px;font-size:18px;font-weight:600;line-height:24px}
.dots{position:absolute;top:536px;left:563px;display:flex;gap:14px}
.dots span{width:8px;height:8px;border-radius:50%;background:#bbb}
.dots span.on{background:var(--green)}
/* newsletter */
.newsletter{top:3433px;left:156px;width:888px;height:168px;background:#fbf0d3;overflow:hidden}
.nl-left{position:absolute;left:0;top:0;width:356px;height:168px;background:var(--orange)}
.nl-left small{position:absolute;left:51px;top:38px;color:#fff;font-size:15px}
.nl-left h2{position:absolute;left:51px;top:62px;color:#fff;font-size:34px;font-weight:500;line-height:39px}
.nl-right p{position:absolute;left:442px;top:36px;font-size:17px}
.nl-form{position:absolute;left:424px;top:87px;display:flex}
.nl-form .field{width:226px;height:44px;background:#fff;border-radius:22px 0 0 22px;padding-left:22px;font-size:14px;color:var(--muted);display:flex;align-items:center}
.nl-form .send{width:168px;height:44px;background:var(--green);color:#fff;font-weight:600;font-size:18px;border-radius:0 22px 22px 0;display:flex;align-items:center;justify-content:center}
/* footer */
footer{top:3640px;height:360px}
footer .rule{position:absolute;left:156px;width:888px;height:1px;background:var(--line)}
.vline{position:absolute;top:0;width:1px;height:300px;background:var(--line)}
.contact{position:absolute;left:156px;display:flex;gap:22px;align-items:flex-start}
.contact .ico{width:46px;height:46px;border-radius:50%;background:#eef0ec;display:flex;align-items:center;justify-content:center;flex:none}
.contact b{display:block;font-size:16px;font-weight:600}
.contact span{font-size:15px;line-height:20px}
.foot-logo{position:absolute;left:490px;top:60px;display:flex;align-items:center;gap:8px}
.foot-logo .mark{width:34px;height:34px;border-radius:50%;border:3px solid var(--ink)}
.foot-logo .name{font-size:22px;font-weight:600}
.foot-about{position:absolute;left:456px;top:142px;width:290px;text-align:center;font-size:14px;line-height:21px;color:var(--text);font-weight:300}
.foot-social{position:absolute;left:496px;top:232px;display:flex;gap:22px}
.foot-social span{width:36px;height:36px;border-radius:50%;background:#eef0ec;display:flex;align-items:center;justify-content:center}
.foot-social span i{width:12px;height:12px;border-radius:50%;background:var(--ink)}
.links{position:absolute;left:820px;top:64px}
.links h4{font-size:16px;font-weight:600}
.links ul{list-style:none;display:grid;grid-template-columns:145px 80px;row-gap:16px;margin-top:22px;font-size:15px;color:var(--text)}
.copy{position:absolute;top:324px;width:1200px;text-align:center;font-size:14px;color:var(--text)}
</style>
</head>
<body>

<div class="topbar">
  <div class="wrap"><span>Welcome to Veltrana Swiss AG</span>
    <div class="social"><span></span><span></span><span></span><span></span></div>
  </div>
</div>

<header>
  <div class="logo"><span class="mark"></span><span class="name">Veltrana Swiss AG</span></div>
  <div class="nav-divider"></div>
  <nav><span>About</span><span>Our Ingredients</span><span>Partners</span><span>News</span><span>Contact</span></nav>
  <div class="head-tools">
    <div class="tool"><svg width="14" height="14" viewBox="0 0 14 14" fill="none" stroke="#333" stroke-width="1.5"><circle cx="6" cy="6" r="4.5"/><path d="M9.5 9.5l3 3"/></svg></div>
    <div class="sep"></div>
    <div class="tool" style="background:#eee"><svg width="16" height="16" viewBox="0 0 16 16" fill="none" stroke="#333" stroke-width="1.3"><circle cx="8" cy="8" r="7"/><circle cx="8" cy="6.5" r="2.5"/><path d="M3.5 13c1-2 2.7-3 4.5-3s3.5 1 4.5 3"/></svg></div>
    <div class="tool" style="background:#eee"><span class="flag"></span></div>
  </div>
</header>

<section class="hero" role="img" aria-label="Terraced green tea plantation on hills at sunrise">
  <div class="hero-label">100 % Natural Ingredients</div>
  <h1>Natural &amp; Functional<br>Ingredients Trader</h1>
  <span class="btn">Discover Now <span class="arrow"><svg width="12" height="12" viewBox="0 0 12 12" fill="none" stroke="#333" stroke-width="1.6"><path d="M2 6h8M7 3l3 3-3 3"/></svg></span></span>
  <span class="slide-arrow" style="left:53px"><svg width="16" height="16" viewBox="0 0 16 16" fill="none" stroke="#222" stroke-width="1.6"><path d="M14 8H2M6 4L2 8l4 4"/></svg></span>
  <span class="slide-arrow" style="left:1106px"><svg width="16" height="16" viewBox="0 0 16 16" fill="none" stroke="#222" stroke-width="1.6"><path d="M2 8h12M10 4l4 4-4 4"/></svg></span>
</section>

<section class="perks">
  <div class="perk" style="left:157px">
    <svg width="44" height="44" viewBox="0 0 44 44" fill="none" stroke="#333" stroke-width="1.6"><circle cx="22" cy="22" r="18"/><ellipse cx="22" cy="22" rx="8" ry="18"/><path d="M4 22h36M7 13h30M7 31h30"/></svg>
    <div><b>Worldwide sourcing</b><small>Delivery from just $9.50</small></div>
  </div>
  <div class="perk" style="left:460px">
    <svg width="44" height="44" viewBox="0 0 44 44" fill="none" stroke="#333" stroke-width="1.6"><circle cx="22" cy="18" r="12"/><circle cx="22" cy="18" r="7"/><path d="M14 28l-4 12 6-3 3 5 3-9M30 28l4 12-6-3-3 5-3-9"/></svg>
    <div><b>Best Quality</b><small>ISO 22000 certified</small></div>
  </div>
  <div class="perk" style="left:764px">
    <svg width="44" height="44" viewBox="0 0 44 44" fill="none" stroke="#333" stroke-width="1.6"><path d="M8 26v-4a14 14 0 0 1 28 0v4"/><rect x="5" y="24" width="7" height="11" rx="3"/><rect x="32" y="24" width="7" height="11" rx="3"/><path d="M36 35c0 4-5 5-10 5"/></svg>
    <div><b>Expert Support Team</b><small>Customer 48 hours resolve</small></div>
  </div>
</section>

<section class="values">
  <div class="eyebrow" style="top:62px">Features</div>
  <div class="title" style="top:86px">Our Values</div>
  <div class="bottle" role="img" aria-label="Amber dropper bottle with hemp leaves and softgel capsules"></div>
  <div class="pill" style="left:157px;top:164px"><span class="ico"><svg width="26" height="26" viewBox="0 0 26 26"><circle cx="13" cy="13" r="12" fill="#e8f5e0"/><path d="M7 19c0-8 6-12 12-12-1 7-5 12-12 12z" fill="#3aa537"/></svg></span>Sourcing of Natural and<br>Health Ingredients</div>
  <div class="pill" style="left:157px;top:248px"><span class="ico"><svg width="26" height="26" viewBox="0 0 26 26"><path d="M13 22L4 13a5 5 0 0 1 9-6 5 5 0 0 1 9 6z" fill="#e63946"/><path d="M5 13h5l2-3 2 6 2-3h5" fill="none" stroke="#fff" stroke-width="1.4"/></svg></span>Health &amp; Nutritional Health</div>
  <div class="pill" style="left:157px;top:330px"><span class="ico"><svg width="26" height="26" viewBox="0 0 26 26"><circle cx="13" cy="13" r="11" fill="#4fb3e0"/><path d="M6 10c3 0 4 2 6 2s2 4 0 6M15 6c2 2 5 3 5 7" fill="none" stroke="#3aa537" stroke-width="3"/></svg></span>Eco-friendly and Sustainability</div>
  <div class="pill" style="left:157px;top:412px"><span class="ico"><svg width="26" height="26" viewBox="0 0 26 26"><circle cx="13" cy="10" r="8" fill="#f8cf3a"/><path d="M9 16l-2 9 6-3 6 3-2-9z" fill="#f0912c"/></svg></span>High Quality Standard in<br>Products and Logistic Services</div>
  <div class="pill" style="left:718px;top:164px"><span class="ico"><svg width="26" height="26" viewBox="0 0 26 26"><path d="M13 3l9 4v6c0 6-4 9-9 11-5-2-9-5-9-11V7z" fill="#6fa8e6"/><path d="M8 13l4 4 6-7" fill="none" stroke="#fff" stroke-width="2"/></svg></span>Trust and Reliability</div>
  <div class="pill" style="left:718px;top:248px"><span class="ico"><svg width="26" height="26" viewBox="0 0 26 26" fill="none" stroke="#0677ba" stroke-width="2"><circle cx="13" cy="13" r="10"/><circle cx="13" cy="13" r="5"/><path d="M13 1v4M13 21v4M1 13h4M21 13h4"/></svg></span>Flexibility &amp; Speed to Market</div>
  <div class="pill" style="left:718px;top:330px"><span class="ico"><svg width="26" height="26" viewBox="0 0 26 26"><circle cx="13" cy="11" r="7" fill="#ffc000"/><rect x="10" y="18" width="6" height="5" rx="1" fill="#888"/></svg></span>Technical Advice for the<br>Development of New Products</div>
  <div class="pill" style="left:718px;top:412px"><span class="ico"><svg width="26" height="26" viewBox="0 0 26 26"><path d="M13 2l10 4v6c0 7-5 10-10 12C8 22 3 19 3 12V6z" fill="#f8cf3a"/><path d="M8 13l4 4 6-7" fill="none" stroke="#3aa537" stroke-width="2.4"/></svg></span>Security of Supply</div>
</section>

<section class="ingredients">
  <div class="eyebrow" style="top:60px">What We Offer</div>
  <div class="title" style="top:84px">Our Ingredients</div>
  <div class="ing-card" style="left:157px"><div class="photo" role="img" aria-label="Fresh rosemary sprigs with an oil bottle" style="background:linear-gradient(135deg,#f2f0ea,#b8c49a 45%,#d8c070 80%,#ece8de)"></div><div class="tag">Natural Plant Extracts</div></div>
  <div class="ing-card" style="left:460px"><div class="photo" role="img" aria-label="Bowl of fresh fruit, berries and vegetables" style="background:radial-gradient(circle at 50% 55%,#c8323a,#f08a2c 35%,#6aa33a 60%,#f3f1ec 90%)"></div><div class="tag">Natural Vitamins</div></div>
  <div class="ing-card" style="left:764px"><div class="photo" role="img" aria-label="Wooden box of dried fruits and nuts" style="background:radial-gradient(circle at 55% 50%,#e8a040,#b85a2a 35%,#efe9e4 75%)"></div><div class="tag">Vegan Ingredients</div></div>
  <span class="btn">View All <span class="arrow"><svg width="12" height="12" viewBox="0 0 12 12" fill="none" stroke="#333" stroke-width="1.6"><path d="M2 6h8M7 3l3 3-3 3"/></svg></span></span>
</section>

<section class="offer">
  <div class="offer-photo" role="img" aria-label="Apricots on a wooden board with green leaves and white flowers"></div>
  <h2>Get 10% off on Natural<br>Anti-oxidants</h2>
  <div class="grab">Grab The Offer</div>
  <div class="count">
    <div><span>4</span><small>DAYS</small></div>
    <div><span>12</span><small>HOURS</small></div>
    <div><span>55</span><small>MINUTES</small></div>
    <div><span>15</span><small>SECONDS</small></div>
  </div>
  <span class="btn">Shop Now <span class="arrow"><svg width="12" height="12" viewBox="0 0 12 12" fill="none" stroke="#333" stroke-width="1.6"><path d="M2 6h8M7 3l3 3-3 3"/></svg></span></span>
</section>

<section class="about">
  <div class="about-photo" role="img" aria-label="Hand picking ripe red coffee cherries from a green bush"></div>
  <div class="eyebrow">About Us</div>
  <h2>We Grow Pure,<br>Organic Products</h2>
  <p>Veltrana Swiss AG in Brunnwil is a Company limited by shares (AG) from the sector in Trading in food products. The purpose of the company is the production of and trade in food, food additives, raw materials and active ingredients, taking on representations, technical advice and trade.</p>
  <span class="btn">Learn More <span class="arrow"><svg width="12" height="12" viewBox="0 0 12 12" fill="none" stroke="#333" stroke-width="1.6"><path d="M2 6h8M7 3l3 3-3 3"/></svg></span></span>
</section>

<section class="news">
  <div class="eyebrow" style="top:62px">Articles</div>
  <div class="title" style="top:86px">Our Latest News</div>
  <article class="post" style="left:156px"><div class="photo" role="img" aria-label="Orange cordyceps on a wooden surface" style="background:radial-gradient(circle at 50% 50%,#f07a20,#c86a30 35%,#8a7a6a 75%)"></div><div class="date">10<span>Apr</span></div><div class="meta">By Lena Hofer<i>|</i>3 Comments</div><h3>Medicinal Values &amp; Prospect of Cordyceps Extract</h3></article>
  <article class="post" style="left:460px"><div class="photo" role="img" aria-label="Rosemary with oil bottles on a wooden table" style="background:linear-gradient(135deg,#b89a6a,#7a8a3a 45%,#c08a30 75%,#a07a4a)"></div><div class="date">10<span>Apr</span></div><div class="meta">By Lena Hofer<i>|</i>3 Comments</div><h3>Rosemary Extract: Natural Antioxidant and Preservative</h3></article>
  <article class="post" style="left:764px"><div class="photo" role="img" aria-label="Cranberry tart with fresh berries" style="background:radial-gradient(circle at 35% 40%,#b0182a,#8a1020 35%,#6a8a5a 70%,#dde0da)"></div><div class="date">10<span>Apr</span></div><div class="meta">By Lena Hofer<i>|</i>3 Comments</div><h3>Market Segmentation of Cranberry Extract</h3></article>
  <div class="dots"><span></span><span class="on"></span><span></span><span></span></div>
</section>

<section class="newsletter">
  <div class="nl-left"><small>Don't Miss Our Deals</small><h2>Exclusive Offers<br>&amp; Sale</h2></div>
  <div class="nl-right"><p>Sign up and get a voucher of worth $250.00</p>
    <div class="nl-form"><span class="field">Email address</span><span class="send">Subscribe</span></div>
  </div>
</section>

<footer>
  <div class="rule" style="top:0"></div>
  <div class="vline" style="left:420px"></div>
  <div class="vline" style="left:780px"></div>
  <div class="contact" style="top:58px"><span class="ico"><svg width="18" height="18" viewBox="0 0 18 18" fill="none" stroke="#333" stroke-width="1.3"><rect x="2" y="4" width="14" height="10" rx="1"/><path d="M2 5l7 5 7-5"/></svg></span><div><b>Email</b><span>info@veltranaswiss.com</span></div></div>
  <div class="contact" style="top:130px"><span class="ico"><svg width="18" height="18" viewBox="0 0 18 18" fill="none" stroke="#333" stroke-width="1.3"><path d="M4 2l3 1 1 4-2 1c1 2 2 3 4 4l1-2 4 1 1 3-2 2C8 16 2 10 2 4z"/></svg></span><div><b>Phone</b><span>020.4.117.382</span></div></div>
  <div class="contact" style="top:202px"><span class="ico"><svg width="18" height="18" viewBox="0 0 18 18" fill="none" stroke="#333" stroke-width="1.3"><path d="M9 17s6-6 6-10A6 6 0 0 0 3 7c0 4 6 10 6 10z"/><circle cx="9" cy="7" r="2"/></svg></span><div><b>Address</b><span>Lindenweg 14, 8725<br>Brunnwil Switzerland</span></div></div>
  <div class="foot-logo"><span class="mark"></span><span class="name">Veltrana Swiss AG</span></div>
  <p class="foot-about">Veltrana Swiss AG in Brunnwil is a Company limited by shares (AG) from the sector in Trading in food products.</p>
  <div class="foot-social"><span><i></i></span><span><i></i></span><span><i></i></span><span><i></i></span></div>
  <div class="links"><h4>Important Links</h4>
    <ul><li>About</li><li>Account</li><li>Our Ingredients</li><li>Help</li><li>Partners</li><li>Support</li><li>News</li><li>FAQ</li><li>Contact</li></ul>
  </div>
  <div class="rule" style="top:302px"></div>
  <div class="copy">© Copyright 2022 Veltrana Swiss AG. All Rights Reserved.</div>
</footer>

</body>
</html>
```